Mobile Fitness snd Therapy Business Card Design

I need a business card designed for my mobile fitness and therapy business.

Please view the images that I have uploaded. I like the simplicity of the design that I have attached. I adapted it with my information

Target Market(s)

Those seeking personal training, injury rehabilitation or massage therapy.

Industry/Entity Type

Business

Contact Information for Business Card

Derek Fulham - MSc, CAT(C), RMT, CSCS, Pn2
e-mail: derek@vantrelo.com
website: www.vantrelo.com
instagram: @derek_fulham

Font styles to use
Sans Serif

Colors
3176b5
0355a3

Requirements
Must have
• "Contact us to receive a FREE assessment"
• Services offered:
• Personal Training
• Golf Fitness
• Injury Rehab
• Massage Therapy
• Yoga
Nice to have
• Consistent colours with brand
• - Dark Blue: #232837
• - Blue: #5096f0
• Consistent look/feel with the website: www.vantrelo.com

```html
<!DOCTYPE html>
<html lang="en">
<head>
<meta charset="utf-8">
<title>Vantrelo Business Card</title>
<link rel="stylesheet" href="https://fonts.googleapis.com/css2?family=Open+Sans:wght@400;600;700&display=swap">
<style>
  :root {
    --backdrop: #c2c2c2;
    --card-white: #ffffff;
    --navy: #232837;
    --accent-blue: #1f56d0;
    --text-dark: #1d2230;
    --rule-grey: #bdbdbd;
    --shadow: rgba(0, 0, 0, 0.35);
  }
  * { margin: 0; padding: 0; box-sizing: border-box; }
  html, body {
    width: 1200px; height: 900px; overflow: hidden;
    background: var(--backdrop);
    font-family: "Open Sans", Arial, sans-serif;
  }
  .canvas { position: relative; width: 1200px; height: 900px; }

  .card {
    position: absolute; top: 170px; width: 347px; height: 560px;
    background: var(--card-white);
    box-shadow: 3px 4px 6px var(--shadow);
    overflow: hidden;
  }
  .card--front { left: 259px; }
  .card--back { left: 631px; }

  /* Front */
  .brand {
    position: absolute; top: 50px; left: 0; width: 100%;
    text-align: center;
  }
  .brand__name {
    font-size: 40px; font-weight: 600; letter-spacing: 3px;
    color: var(--navy); line-height: 1;
  }
  .brand__tagline {
    margin-top: 12px; font-size: 12.5px; font-weight: 700;
    letter-spacing: 2px; color: var(--navy);
  }
  .identity {
    position: absolute; top: 368px; left: 0; width: 100%;
    text-align: center;
  }
  .identity__name {
    font-size: 21px; font-weight: 600; color: var(--accent-blue);
    text-transform: uppercase; letter-spacing: 0.3px; line-height: 1.2;
  }
  .identity__credentials {
    margin-top: 4px; font-size: 13.5px; color: var(--text-dark);
  }
  .identity__rule {
    width: 136px; height: 1px; margin: 13px auto 14px;
    background: var(--rule-grey);
  }
  .contact-list { list-style: none; }
  .contact-list li {
    font-size: 16.5px; color: var(--text-dark); line-height: 23px;
  }
  .contact-list .label { color: var(--accent-blue); font-weight: 600; }

  /* Back */
  .back__panel {
    position: absolute; top: 0; left: 75px; right: 0; bottom: 0;
    background: var(--navy);
  }
  .back__offer {
    position: absolute; left: 37px; top: 280px;
    transform: translate(-50%, -50%) rotate(-90deg);
    white-space: nowrap;
    font-size: 24px; font-weight: 600; color: var(--navy);
  }
  .services {
    position: absolute; top: 287px; left: 113px; color: var(--card-white);
  }
  .services__title {
    font-size: 18.5px; font-weight: 600; text-decoration: underline;
    text-underline-offset: 4px; letter-spacing: 0.2px;
  }
  .services__list { list-style: none; margin-top: 34px; }
  .services__list li {
    display: flex; align-items: center; gap: 9px;
    font-size: 20.5px; font-weight: 600; line-height: 38px;
  }
  .services__list svg { width: 18px; height: 22px; flex: none; }
</style>
</head>
<body>
<main class="canvas">
  <section class="card card--front" aria-label="Business card front">
    <header class="brand">
      <div class="brand__name">VANTRELO</div>
      <div class="brand__tagline">NUTRITION - FITNESS - HEALTH</div>
    </header>
    <div class="identity">
      <div class="identity__name">Derek Fulham</div>
      <div class="identity__credentials">MSc, CAT(C), RMT, CSCS, Pn2</div>
      <div class="identity__rule"></div>
      <ul class="contact-list">
        <li><span class="label">E</span>: derek@vantrelo.com</li>
        <li><span class="label">W</span>: www.vantrelo.com</li>
        <li><span class="label">I</span>: @derek_fulham</li>
      </ul>
    </div>
  </section>

  <section class="card card--back" aria-label="Business card back">
    <div class="back__offer">Contact us to receive a FREE assessment</div>
    <div class="back__panel"></div>
    <div class="services">
      <h2 class="services__title">SERVICES OFFERED</h2>
      <ul class="services__list">
        <li><svg viewBox="0 0 18 22"><polygon points="9,1 17,11 9,21 1,11" fill="#fff"/></svg>Personal Training</li>
        <li><svg viewBox="0 0 18 22"><polygon points="9,1 17,11 9,21 1,11" fill="#fff"/></svg>Golf Fitness</li>
        <li><svg viewBox="0 0 18 22"><polygon points="9,1 17,11 9,21 1,11" fill="#fff"/></svg>Injury Rehab</li>
        <li><svg viewBox="0 0 18 22"><polygon points="9,1 17,11 9,21 1,11" fill="#fff"/></svg>Massage Therapy</li>
        <li><svg viewBox="0 0 18 22"><polygon points="9,1 17,11 9,21 1,11" fill="#fff"/></svg>Yoga</li>
      </ul>
    </div>
  </section>
</main>
</body>
</html>
```